Oversized Postcard for Estate Planning & Probate 1st 2nd and 3rd prizes

Create a professional, fresh and polished oversized post card for law firm specializing in Estate Planning & Probate Law for High Net Worth Clients

Use any picture(s) of your choice (mine or ones you recommend), logo, headshot and company info

www.morvenashbylaw.com

Westbrook Office - 4800 Kestrel Avenue, Suite 900, Charlotte, NC 28210
Harlowe Office - 13470 Birch Court, Suite 400, Charlotte, NC 28277

Phone (704) 555-0187

Use this card for a Free Consultation

Target Market(s)

young and old families too; business owners

Industry/Entity Type

Law Firm

Font styles to use
Serif
Sans Serif

Requirements
Must have
• Use any picture(s) of your choice (mine or ones you recommend), logo, headshot and company info
• www.morvenashbylaw.com
• Westbrook Office - 4800 Kestrel Avenue, Suite 900, Charlotte, NC 28210
• Harlowe Office - 13470 Birch Court, Suite 400, Charlotte, NC 28277
• Phone (704) 555-0187
• Use this card for a Free Consultation
Nice to have
• great colors and great design; like graphics with depth /shading
Should not have
• don't use too many pics - keep it simple

```html
<!DOCTYPE html>
<html lang="en">
<head>
<meta charset="utf-8">
<title>Morven Ashby Law – Oversized Postcard</title>
<link href="https://fonts.googleapis.com/css2?family=Arvo:wght@700&family=EB+Garamond:wght@400;500&family=Open+Sans:ital,wght@0,300;0,400;0,600;1,600&family=Arimo&display=swap" rel="stylesheet">
<style>
:root{
  --stage:#3d3d3f;
  --navy:#0b4566;
  --teal:#1589b8;
  --teal-mid:#15668f;
  --brand:#1a7fa8;
  --ink:#0d2f45;
  --mist:#e8f0f5;
  --slot:#e6edf5;
  --paper:#fbfbfb;
  --white:#ffffff;
  --sans:'Open Sans',sans-serif;
  --serif:'EB Garamond',serif;
  --slab:'Arvo',serif;
}
*{box-sizing:border-box;margin:0;padding:0}
html,body{width:904px;height:1200px;overflow:hidden;background:var(--stage)}
.card{position:absolute;left:49px;width:809px;box-shadow:4px 4px 8px rgba(0,0,0,.45);overflow:hidden}
.front{top:61px;height:523px;background:var(--mist)}
.back{top:625px;height:524px;background:var(--paper)}
.abs{position:absolute}

/* front */
.top-band{left:0;top:0;width:809px;height:135px;background:var(--navy)}
.top-band-tail{left:440px;top:135px;width:369px;height:10px;background:var(--navy);clip-path:polygon(0 0,100% 0,97% 100%,2% 100%)}
.family-photo{left:0;top:135px;width:470px;height:332px;background:linear-gradient(100deg,#cbb8a3 0%,#9fb4c6 40%,#c6d6e2 72%,rgba(232,240,245,0) 100%)}
.logo-panel{left:58px;top:33px;width:238px;height:150px;background:var(--white);border-radius:6px;display:flex;flex-direction:column;align-items:center;justify-content:center;gap:8px}
.logo-dot{width:56px;height:56px;border-radius:50%;background:var(--navy)}
.brand-name{font-family:var(--sans);font-weight:400;color:var(--brand);font-size:25px;line-height:1;border-top:1px solid #222;padding-top:8px;width:208px;text-align:center}
.brand-sub{display:flex;align-items:center;gap:8px;width:208px;font-family:var(--serif);font-size:13px;letter-spacing:1px;color:#222}
.brand-sub::before,.brand-sub::after{content:"";flex:1;height:1px;background:#222}
.headline{right:37px;top:27px;text-align:right;font-family:var(--slab);font-size:21px;line-height:25px;color:var(--white)}
.services-line{right:37px;top:91px;text-align:right;font-family:var(--sans);font-weight:300;font-size:14px;line-height:21px;color:#dce9f1}
.office{top:143px;height:73px;background:var(--teal);border-radius:0 0 5px 5px;color:var(--white);padding:9px 14px}
.office h3{font-family:var(--sans);font-weight:600;font-size:15px;margin-bottom:4px}
.office p{font-family:var(--sans);font-size:11.5px;line-height:16px}
.office-west{left:367px;width:200px}
.office-harlowe{left:574px;width:201px}
.about{left:390px;top:264px;width:198px;text-align:right;font-family:var(--sans);font-weight:300;font-size:11.3px;line-height:17.6px;color:var(--teal-mid)}
.headshot{left:606px;top:264px;width:169px;height:203px;border-radius:4px 4px 0 0;background:linear-gradient(180deg,#cdbfa8 0%,#b99a6e 45%,#2a2a30 100%)}
.bottom-band{left:0;top:467px;width:809px;height:56px}
.offer{left:29px;top:477px;font-family:var(--sans);font-size:12.5px;line-height:18px;color:#e4f1f8;font-weight:300}
.offer em{font-style:italic;font-weight:600;color:var(--white)}
.phone-front{left:213px;top:480px;font-family:var(--sans);font-size:15px;color:var(--white)}
.phone-front span{font-family:var(--serif);font-size:23px}
.web-front{left:482px;top:483px;font-family:var(--serif);font-size:19px;letter-spacing:1.5px;color:var(--white)}

/* back */
.kid-photo{left:0;top:155px;width:567px;height:369px;background:linear-gradient(90deg,#c9b8a2 0%,#d8d2c8 45%,rgba(251,251,251,0) 100%)}
.back-logo{left:46px;top:37px;width:263px;display:flex;flex-direction:column;align-items:center;gap:8px}
.back-logo .brand-name{width:263px;font-size:32px;padding-top:12px}
.back-logo .brand-sub{width:263px;font-size:15px}
.tagline{left:46px;top:113px;font-family:var(--serif);font-size:14px;letter-spacing:1.2px;color:#2a8fba}
.contact-box{left:326px;top:38px;width:317px;height:70px;background:var(--navy);text-align:center;padding-top:10px}
.email{font-family:var(--sans);font-weight:300;font-size:17px;letter-spacing:.8px;color:#a9c6d6}
.web-back{font-family:var(--serif);font-size:18px;letter-spacing:1.3px;color:var(--white);margin-top:5px}
.phone-back{left:346px;top:114px;font-family:var(--serif);font-size:41px;letter-spacing:1px;color:var(--ink)}
.sign-name{left:362px;top:190px;width:160px;text-align:center;font-family:var(--sans);font-size:17px;color:var(--brand)}
.service-list{left:360px;top:245px;width:161px;list-style:none}
.service-list li{font-family:var(--sans);font-weight:300;font-size:15px;line-height:25px;text-align:center;color:var(--brand);border-bottom:1px solid #c9d3da;height:26px}
.service-list li:last-child{border-bottom:none}
.slot{background:var(--slot);font-family:'Arimo',sans-serif;font-size:14px;color:#000;text-align:center}
.postage{left:678px;top:13px;width:117px;height:116px;padding-top:40px;line-height:18px}
.address{left:538px;top:230px;width:257px;height:282px;padding-top:50px}
.barcode{left:350px;top:454px;width:188px;height:58px}
.barcode-label{left:350px;top:476px;width:445px}
</style>
</head>
<body>

<section class="card front">
  <div class="abs family-photo" role="img" aria-label="Photo of a smiling multi-generation family walking hand in hand along a sunny beach"></div>
  <div class="abs top-band"></div>
  <div class="abs top-band-tail"></div>

  <div class="abs logo-panel">
    <div class="logo-dot"></div>
    <div class="brand-name">Morven Ashby</div>
    <div class="brand-sub">LAW PLLC</div>
  </div>

  <h1 class="abs headline">Serving clients with compassion<br>and legal guidance is our passion...</h1>
  <p class="abs services-line">Estate Administration, Probate Law, Estate Planning, Wills,<br>Trusts, Living Wills, Healthcare Powers</p>

  <div class="abs office office-west">
    <h3>Westbrook Office</h3>
    <p>4800 Kestrel Avenue, Suite 900,<br>Charlotte, NC 28210</p>
  </div>
  <div class="abs office office-harlowe">
    <h3>Harlowe Office</h3>
    <p>13470 Birch Court, Suite 400,<br>Charlotte, NC 28277</p>
  </div>

  <p class="abs about">Morven Ashby Law, PLLC serving clients in estate planning, estate administration, probate law, wills, revocable trusts, irrevocable trusts, powers of attorney, health care powers of attorney, living wills, hipaa releases, guardianships, special needs planning, wealth transfers, elder law and business law in North Carolina and South Carolina.</p>

  <div class="abs headshot" role="img" aria-label="Professional headshot of the attorney in a dark blazer"></div>

  <svg class="abs bottom-band" width="809" height="56" viewBox="0 0 809 56" aria-hidden="true">
    <rect width="809" height="56" fill="#15668f"/>
    <polygon points="0,0 250,0 195,56 0,56" fill="#1a86b3"/>
    <polygon points="590,0 809,0 809,56 540,56" fill="#0b4566"/>
  </svg>
  <p class="abs offer">Use this card for a<br><em>Free Consultation</em></p>
  <p class="abs phone-front">Phone: <span>(704) 555-0187</span></p>
  <p class="abs web-front">WWW.MORVENASHBYLAW.COM</p>
</section>

<section class="card back">
  <div class="abs kid-photo" role="img" aria-label="Photo of a toddler in an aviator cap and scarf holding up a toy airplane in a bright playroom"></div>

  <div class="abs back-logo">
    <div class="brand-name">Morven Ashby</div>
    <div class="brand-sub">LAW PLLC</div>
  </div>
  <p class="abs tagline">BIG THINGS START FROM LITTLE IDEAS</p>

  <div class="abs contact-box">
    <p class="email">morven@morvenashbylaw.com</p>
    <p class="web-back">WWW.MORVENASHBYLAW.COM</p>
  </div>
  <p class="abs phone-back">(704) 555-0187</p>

  <p class="abs sign-name">Morven Ashby</p>
  <ul class="abs service-list">
    <li>Estate Administration</li>
    <li>Probate Law</li>
    <li>Estate Planning</li>
    <li>Wills</li>
    <li>Trusts</li>
    <li>Living Wills</li>
    <li>Healthcare Powers</li>
  </ul>

  <div class="abs slot postage">Postage<br>Area</div>
  <div class="abs slot address">Address Area</div>
  <div class="abs slot barcode"></div>
  <div class="abs slot barcode-label" style="background:transparent">Barcode Area</div>
</section>

</body>
</html>
```